business card - Helicopter Flight Services, Flight School, etc.

We need a business card design for a new helicopter service.

We offer Helicopter Flight Services, Aerial Filming & Photography, Flight School, and Helicopter Tours. In that order.

Summit BladeAir, Inc.
Dennis Tollerby
SummitBladeair@Kestmail.com
626-418-7352

Based at the Brenwick Airport in Van Nuys, CA. The final design should communicate integrity and safety. Pictures or logos at your discretion.

Card back side - surprise me.

```html
<!DOCTYPE html>
<html lang="en">
<head>
<meta charset="utf-8">
<title>Summit BladeAir, Inc. – Business Card</title>
<link rel="stylesheet" href="https://fonts.googleapis.com/css2?family=Open+Sans:wght@400;600;700&display=swap">
<style>
  :root {
    --page-bg: #e9e6e1;
    --blue-light: #3eaadf;
    --blue-deep: #0b5ca8;
    --blue-text: #2a82cc;
    --blue-brand: #1f6fbd;
    --green: #6cb33f;
    --white: #ffffff;
    --card-shadow: 0 10px 28px rgba(40, 30, 20, 0.22);
  }
  * { box-sizing: border-box; margin: 0; padding: 0; }
  html, body {
    width: 1200px;
    height: 913px;
    overflow: hidden;
    background: var(--page-bg);
    font-family: "Open Sans", Arial, sans-serif;
  }
  .canvas {
    position: relative;
    width: 1200px;
    height: 913px;
  }
  .card {
    position: absolute;
    width: 560px;
    height: 320px;
    overflow: hidden;
    box-shadow: var(--card-shadow);
  }

  /* Front */
  .card-front {
    left: 70px;
    top: 110px;
    background: linear-gradient(160deg, var(--blue-light) 0%, #1f82c9 45%, var(--blue-deep) 100%);
  }
  .front-rule {
    position: absolute;
    left: 0;
    top: 214px;
    width: 560px;
    height: 1px;
    background: rgba(255, 255, 255, 0.85);
  }
  .front-corner {
    position: absolute;
    left: 400px;
    top: 215px;
    width: 160px;
    height: 105px;
    background: var(--white);
  }
  .front-band {
    position: absolute;
    left: 0;
    top: 296px;
    width: 400px;
    height: 24px;
    background: var(--green);
  }
  .brand-front {
    position: absolute;
    left: 60px;
    top: 92px;
    display: flex;
    align-items: center;
    gap: 12px;
    color: var(--white);
    font-weight: 700;
    font-size: 30px;
    letter-spacing: 0.5px;
  }
  .brand-dot {
    width: 16px;
    height: 16px;
    border-radius: 50%;
    background: currentColor;
  }
  .holder-name {
    position: absolute;
    left: 26px;
    top: 180px;
    color: var(--white);
    font-weight: 700;
    font-size: 21px;
  }
  .holder-role {
    position: absolute;
    left: 26px;
    top: 219px;
    color: var(--green);
    font-size: 14px;
  }
  .contact-list {
    position: absolute;
    left: 48px;
    top: 244px;
    list-style: none;
    color: var(--white);
    font-size: 15px;
    line-height: 23px;
  }
  .contact-list li { display: flex; align-items: center; gap: 8px; }
  .contact-icon { width: 13px; height: 13px; flex: none; }

  /* Back */
  .card-back {
    left: 570px;
    top: 490px;
    background: var(--white);
    display: flex;
    flex-direction: column;
    align-items: center;
    justify-content: center;
    text-align: center;
  }
  .brand-back {
    display: flex;
    align-items: center;
    gap: 12px;
    color: var(--blue-brand);
    font-weight: 700;
    font-size: 32px;
    letter-spacing: 0.5px;
    margin-bottom: 26px;
  }
  .service-list {
    list-style: none;
    color: var(--blue-text);
    font-size: 16px;
    line-height: 22px;
  }
</style>
</head>
<body>
<main class="canvas">

  <section class="card card-front" aria-label="Card front">
    <div class="front-rule"></div>
    <div class="front-corner"></div>
    <div class="front-band"></div>

    <div class="brand-front"><span class="brand-dot"></span>Summit BladeAir, Inc.</div>

    <h1 class="holder-name">Dennis Tollerby</h1>
    <p class="holder-role">Owner</p>

    <ul class="contact-list">
      <li>
        <svg class="contact-icon" viewBox="0 0 16 16" aria-hidden="true">
          <path d="M3.5 1.5l2.5 0 1 3.5-1.8 1.2c.8 1.8 2.2 3.2 4 4l1.2-1.8 3.5 1v2.5c0 .8-.7 1.5-1.5 1.5C6.9 13.4 2.6 9.1 2 3c0-.8.7-1.5 1.5-1.5z" fill="var(--green)"/>
        </svg>
        626-418-7352
      </li>
      <li>
        <svg class="contact-icon" viewBox="0 0 16 16" aria-hidden="true">
          <rect x="1.5" y="3.5" width="13" height="9" fill="none" stroke="var(--green)" stroke-width="1.6"/>
          <path d="M1.5 3.5l6.5 5 6.5-5" fill="none" stroke="var(--green)" stroke-width="1.6"/>
        </svg>
        SummitBladeair@Kestmail.com
      </li>
    </ul>
  </section>

  <section class="card card-back" aria-label="Card back">
    <div class="brand-back"><span class="brand-dot"></span>Summit BladeAir, Inc.</div>
    <ul class="service-list">
      <li>Aerial Filming &amp; Photography</li>
      <li>Flight School</li>
      <li>Helicopter Tours (In that order)</li>
    </ul>
  </section>

</main>
</body>
</html>
```